I am a home builder and developer

I would like some sort of architectural design like a pencil type of drawing of a house but want it to be professional looking and two sided.

Simply I am a custom home builder and land developer. I would like a new design other than what I have now that's what I thought y'all did. I like mostly black maybe with an pencil type of drawing of a house. Like an architectural look.

Industry/Entity Type

Home Builder

```html
<!DOCTYPE html>
<html lang="en">
<head>
<meta charset="utf-8">
<title>Harlow Ridge Homes – Business Card</title>
<link rel="stylesheet" href="https://fonts.googleapis.com/css2?family=Oswald:wght@600&family=Open+Sans:wght@400;600&display=swap">
<style>
  :root {
    --backdrop-light: #a3a3a3;
    --backdrop-dark: #6e6e6e;
    --card-black: #222223;
    --card-edge: #2c2c2d;
    --silver: #c9c9c9;
    --white: #f4f4f4;
    --text-grey: #cfcfcf;
    --accent-blue: #2fa3de;
    --divider: #6a6a6a;
  }
  * { margin: 0; padding: 0; box-sizing: border-box; }
  html, body { width: 1200px; height: 1000px; overflow: hidden; }
  body {
    background: radial-gradient(ellipse at 60% 40%, var(--backdrop-light) 0%, var(--backdrop-dark) 80%);
    font-family: "Open Sans", sans-serif;
    position: relative;
  }
  .card {
    position: absolute;
    width: 580px;
    height: 340px;
    border-radius: 30px;
    background: linear-gradient(160deg, var(--card-edge), var(--card-black));
    box-shadow: 0 18px 40px rgba(0,0,0,0.35);
  }
  .card-front { left: 60px; top: 130px; }
  .card-back { left: 560px; top: 530px; }

  .brand {
    position: absolute;
    inset: 0;
    display: flex;
    align-items: center;
    justify-content: center;
    gap: 16px;
  }
  .brand-mark {
    width: 34px; height: 34px;
    background: var(--silver);
  }
  .brand-name {
    font-family: "Oswald", sans-serif;
    font-weight: 600;
    font-size: 40px;
    letter-spacing: 2px;
    color: var(--silver);
    text-transform: uppercase;
  }

  .identity {
    position: absolute;
    right: 330px;
    top: 118px;
    text-align: right;
  }
  .person-name {
    font-family: "Oswald", sans-serif;
    font-weight: 600;
    font-size: 34px;
    line-height: 1.05;
    color: var(--white);
    text-transform: uppercase;
  }
  .person-title {
    font-size: 18px;
    font-weight: 600;
    color: var(--accent-blue);
  }
  .divider {
    position: absolute;
    left: 270px;
    top: 100px;
    width: 1px;
    height: 98px;
    background: var(--divider);
  }
  .contacts {
    position: absolute;
    left: 290px;
    top: 104px;
    list-style: none;
  }
  .contacts li {
    display: flex;
    align-items: center;
    gap: 12px;
    font-size: 15px;
    color: var(--text-grey);
    height: 30px;
  }
  .contacts svg, .address svg { width: 14px; height: 14px; fill: var(--accent-blue); flex: none; }
  .web-domain { color: var(--accent-blue); }
  .address {
    position: absolute;
    left: 0; right: 0;
    bottom: 46px;
    display: flex;
    justify-content: center;
    align-items: center;
    gap: 10px;
    font-size: 16px;
    color: var(--text-grey);
  }
</style>
</head>
<body>

  <section class="card card-front">
    <div class="brand">
      <span class="brand-mark"></span>
      <span class="brand-name">Harlow Ridge Homes</span>
    </div>
  </section>

  <section class="card card-back">
    <div class="identity">
      <div class="person-name">Dorian Kell</div>
      <div class="person-title">Chief Engineer</div>
    </div>
    <span class="divider"></span>
    <ul class="contacts">
      <li>
        <svg viewBox="0 0 24 24" aria-hidden="true"><path d="M6.6 10.8a15.1 15.1 0 0 0 6.6 6.6l2.2-2.2c.3-.3.7-.4 1-.2 1.1.4 2.3.6 3.6.6.6 0 1 .4 1 1V20c0 .6-.4 1-1 1A17 17 0 0 1 3 4c0-.6.4-1 1-1h3.5c.6 0 1 .4 1 1 0 1.3.2 2.5.6 3.6.1.3 0 .7-.2 1z"/></svg>
        555-014-2287
      </li>
      <li>
        <svg viewBox="0 0 24 24" aria-hidden="true"><path d="M2 5h20v14H2z M3.5 6.5 12 13l8.5-6.5" stroke="#222223" stroke-width="1.6"/></svg>
        harlowridgehomes@mail.com
      </li>
      <li>
        <svg viewBox="0 0 24 24" aria-hidden="true"><circle cx="12" cy="12" r="10"/><path d="M2 12h20M12 2c3 3 3 17 0 20M12 2c-3 3-3 17 0 20" stroke="#222223" stroke-width="1.4" fill="none"/></svg>
        <span>www.<span class="web-domain">harlowridgehomes</span>.com</span>
      </li>
    </ul>
    <div class="address">
      <svg viewBox="0 0 24 24" aria-hidden="true"><path d="M12 2a7 7 0 0 0-7 7c0 5 7 13 7 13s7-8 7-13a7 7 0 0 0-7-7zm0 9.5A2.5 2.5 0 1 1 12 6.5a2.5 2.5 0 0 1 0 5z"/></svg>
      Your Street Address, Singapore, 1234
    </div>
  </section>

</body>
</html>
```